Single-sided business card for restaurant velmora with new logo made on this site

Business card options with new logo including restaurant name, address, phone number and website. This business card is single-sided only and will be presented at the hostess desk for clients to take. I would like to see options based on a cream card background, a white card background, a yellow card background and a burgundy colored background. It needs to be elegant and traditional.

Target Market(s)

local and international crowd

Industry/Entity Type

restaurant

Contact Information for Business Card

address, website and phone number

Font styles to use
Serif

Colors
EE7325
F08F49
F5BC92
FAE3D3
FDF4ED

Requirements
Must have
• new logo, address, phone number, website
Should not have
• more than three colors

```html
<!DOCTYPE html>
<html lang="es">
<head>
<meta charset="utf-8">
<title>Velmora – Tarjeta de presentación</title>
<link href="https://fonts.googleapis.com/css2?family=Cinzel:wght@400;500;600&display=swap" rel="stylesheet">
<style>
  :root {
    --backdrop: #ababab;
    --card: #ffffff;
    --ink: #3a1a1c;
    --gold: #f2b02e;
    --rule-fade: rgba(58, 26, 28, 0);
  }
  * { margin: 0; padding: 0; box-sizing: border-box; }
  html, body {
    width: 1200px;
    height: 1200px;
    overflow: hidden;
    background: var(--backdrop);
  }
  .business-card {
    position: absolute;
    left: 379px;
    top: 238px;
    width: 442px;
    height: 723px;
    background: var(--card);
    border: 1px solid var(--ink);
    font-family: "Cinzel", "Times New Roman", serif;
    color: var(--ink);
    text-align: center;
  }
  .brand-square {
    position: absolute;
    left: 146px;
    top: 85px;
    width: 140px;
    height: 140px;
    background: var(--gold);
  }
  .brand-name {
    position: absolute;
    left: 0;
    right: 0;
    top: 252px;
    font-size: 46px;
    font-weight: 500;
    letter-spacing: 0.16em;
    padding-left: 0.16em;
    line-height: 1;
  }
  .reservations {
    position: absolute;
    left: 0;
    right: 0;
    top: 422px;
  }
  .reservations-label {
    font-size: 26px;
    font-weight: 500;
    letter-spacing: 0.03em;
    line-height: 1;
  }
  .reservations-phone {
    margin-top: 10px;
    font-size: 36px;
    font-weight: 500;
    line-height: 1;
  }
  .divider {
    position: absolute;
    left: 118px;
    width: 206px;
    height: 2px;
    background: linear-gradient(90deg, var(--rule-fade), var(--ink) 20%, var(--ink) 80%, var(--rule-fade));
  }
  .divider--upper { top: 503px; }
  .divider--lower { top: 643px; }
  .address {
    position: absolute;
    left: 0;
    right: 0;
    top: 518px;
    font-style: normal;
    font-size: 23px;
    font-weight: 500;
    line-height: 26px;
    letter-spacing: 0.02em;
  }
  .website {
    position: absolute;
    left: 0;
    right: 0;
    top: 656px;
    font-size: 20px;
    font-weight: 500;
    letter-spacing: 0.03em;
    line-height: 1;
    text-transform: uppercase;
  }
</style>
</head>
<body>
  <section class="business-card">
    <div class="brand-square"></div>
    <div class="brand-name">VELMORA</div>

    <div class="reservations">
      <div class="reservations-label">RESERVACIONES</div>
      <div class="reservations-phone">958-555-0142</div>
    </div>

    <div class="divider divider--upper"></div>

    <address class="address">
      Restaurant Velmora<br>
      Jacaranda 417<br>
      Bahías de Huatulco<br>
      Oaxaca CP 70989
    </address>

    <div class="divider divider--lower"></div>

    <div class="website">www.velmora.com.mx</div>
  </section>
</body>
</html>
```